Manufacturer Website with Home and Product page

We have this website, veltaro.com, but we need another one for the Canadian market. Canadians like to deal with Canadians so we need to gear it to that. It will be a simpler website than the current site.

We will need a design for two pages, one for the home page and one for a product page.

I synthesized all the brief information for the designers here, descriptions for both pages are included:

https://files.brimlodge.net/doc/8qwx3Lm2Rt7Yp0KzVb4Nc6HsJd9FgA1eUi5Tr

Supporting Folder:
https://files.brimlodge.net/folder/7ZpqW3nTx8Kd2LmR5vYb0HcJs

Industry/Entity Type

Tanning Beds, Red Light Beds, Hydro massage beds

Number of Pages Required

2 page

Requirements
Must have
• Two page descriptions: https://files.brimlodge.net/doc/8qwx3Lm2Rt7Yp0KzVb4Nc6HsJd9FgA1eUi5Tr/view
Nice to have
• Information Folder: https://files.brimlodge.net/folder/u/0/7ZpqW3nTx8Kd2LmR5vYb0HcJs

```html
<!DOCTYPE html>
<html lang="en">
<head>
<meta charset="utf-8">
<title>Veltaro Canada — Commercial Tanning, Red Light &amp; Water Massage</title>
<link href="https://fonts.googleapis.com/css2?family=Lato:wght@400;700;900&display=swap" rel="stylesheet">
<style>
:root{
  --brand:#6d7cc0;
  --brand-dark:#5a69ad;
  --ink:#1d1d2b;
  --text:#4a4a58;
  --muted:#707080;
  --panel:#f3f3f6;
  --card:#f6f6f9;
  --white:#ffffff;
  --navy:#0f2240;
  --footer:#7080c2;
}
*{box-sizing:border-box;margin:0;padding:0}
html,body{width:1200px;height:5352px;overflow:hidden}
body{position:relative;font-family:'Lato',sans-serif;color:var(--text);background:var(--white)}
.abs{position:absolute}
a{color:inherit;text-decoration:none}
.btn{position:absolute;display:flex;align-items:center;justify-content:center;background:var(--brand);color:var(--white);font-size:14px;font-weight:400}
/* header */
.site-header{position:absolute;left:0;top:0;width:1200px;height:70px;background:var(--white)}
.brand{position:absolute;font-weight:900;color:var(--brand);letter-spacing:-.5px}
.site-header .brand{left:110px;top:12px;font-size:38px}
.nav{position:absolute;top:27px;left:333px;display:flex;gap:0;font-size:13px;color:var(--ink)}
.nav span{margin-right:38px}
/* hero */
.hero{position:absolute;left:0;top:70px;width:1200px;height:495px;background:linear-gradient(100deg,#eef1f3 0%,#dfe6ea 35%,#bcd3dd 60%,#e8dccb 100%)}
.hero h1{position:absolute;left:113px;top:132px;font-size:33px;line-height:44px;font-weight:900;color:var(--ink);width:440px}
.badge{position:absolute;left:420px;top:385px;width:110px;height:110px;border-radius:50%;background:#d8232a}
/* partners */
.partners{position:absolute;left:0;top:565px;width:1200px;height:200px}
.partners .name{position:absolute;top:68px;font-size:30px;font-weight:700;color:var(--ink);display:flex;align-items:center;gap:8px}
.partners .dot{width:26px;height:26px;border-radius:50%;background:var(--brand)}
/* products */
.products{position:absolute;left:0;top:765px;width:1200px;height:1752px;background:var(--panel)}
.section-title{position:absolute;left:0;width:1200px;text-align:center;font-weight:900;color:var(--ink);font-size:46px}
.photo{position:absolute}
.prod-title{position:absolute;font-size:40px;font-weight:700;color:var(--ink)}
.prod-text{position:absolute;width:360px;font-size:12.5px;line-height:23px;color:var(--text)}
/* specialist */
.specialist{position:absolute;left:0;top:2517px;width:1200px;height:311px;background:linear-gradient(90deg,#0c1a33,#1b3356 55%,#0f2240)}
.specialist h2{position:absolute;left:162px;top:112px;font-size:36px;font-weight:700;color:var(--white)}
.specialist p{position:absolute;left:162px;top:164px;width:480px;font-size:14px;line-height:24px;color:#e4e8f2}
/* industries */
.card{position:absolute;width:275px;height:393px;background:var(--card)}
.card .icon{position:absolute;left:22px;top:28px;width:58px;height:58px;border-radius:50%;background:var(--white)}
.card h3{position:absolute;left:20px;top:112px;font-size:21px;font-weight:700;color:var(--ink)}
.card p{position:absolute;left:20px;top:150px;width:245px;font-size:11.5px;line-height:24.5px;color:var(--text)}
.card .more{position:absolute;left:18px;top:311px;display:flex;align-items:center;gap:10px;font-size:12px;font-weight:700;color:var(--ink)}
.circle{width:52px;height:52px;border-radius:50%;border:1.5px solid var(--ink);display:flex;align-items:center;justify-content:center}
/* salon */
.salon h2{position:absolute;left:162px;top:4172px;font-size:36px;font-weight:700;color:var(--ink)}
.salon .sub{position:absolute;left:162px;top:4230px;font-size:15px;color:var(--ink)}
.step{position:absolute;left:160px;display:flex;align-items:center;gap:18px;font-size:14px;color:var(--ink)}
.step i{width:40px;height:40px;border:1.5px solid var(--brand);border-radius:8px;display:block}
/* footer */
.footer{position:absolute;left:0;top:4715px;width:1200px;height:637px;background:var(--footer);color:var(--white)}
.footer h4{position:absolute;font-size:16px;font-weight:700}
.footer .links{position:absolute;font-size:13px;line-height:32px}
.contact{position:absolute;left:113px;font-size:13px;line-height:18px;display:flex;gap:10px}
.social{position:absolute;top:140px;width:38px;height:38px;border-radius:50%;border:1.5px solid var(--white)}
.search{position:absolute;left:826px;top:213px;width:262px;height:44px;background:var(--white);color:var(--muted);font-size:11px;padding:15px 14px}
.legal{position:absolute;left:110px;top:455px;width:980px;text-align:center;font-size:10.5px;line-height:19px;color:#eef0fa}
.copy{position:absolute;left:0;top:600px;width:1200px;text-align:center;font-size:12px}
</style>
</head>
<body>

<header class="site-header">
  <div class="brand">Veltaro</div>
  <nav class="nav">
    <span>Tanning ▾</span><span>Massage ▾</span><span>Red Light ▾</span><span>Salon Startup</span><span>About Us</span><span>Contact Us</span>
  </nav>
  <a class="btn" style="left:950px;top:18px;width:138px;height:38px">Request A Catalog</a>
</header>

<section class="hero" role="img" aria-label="Woman in sunglasses on a sandy beach beside commercial tanning and red light beds">
  <h1>The Leading Manufacturer In Commercial Tanning, Red Light And Water Massage Therapy</h1>
  <a class="btn" style="left:113px;top:327px;width:126px;height:34px">Contact Us</a>
  <div class="badge"></div>
</section>

<section class="partners">
  <svg class="abs" style="left:102px;top:75px" width="22" height="20"><path d="M20 10H3M9 4 3 10l6 6" stroke="#1d1d2b" stroke-width="2" fill="none"/></svg>
  <div class="name" style="left:160px"><span class="dot"></span>Nordly</div>
  <div class="name" style="left:348px"><span class="dot"></span>Kestra</div>
  <div class="name" style="left:530px"><span class="dot"></span>Olvin</div>
  <div class="name" style="left:722px"><span class="dot"></span>Maplet</div>
  <div class="name" style="left:905px"><span class="dot"></span>Tiven</div>
  <svg class="abs" style="left:1068px;top:75px" width="22" height="20"><path d="M2 10h17M13 4l6 6-6 6" stroke="#1d1d2b" stroke-width="2" fill="none"/></svg>
</section>

<section class="products">
  <h2 class="section-title" style="top:58px">Our Products</h2>

  <div class="photo" style="left:170px;top:175px;width:350px;height:433px;background:linear-gradient(160deg,#6d5bd6,#b44fa5 45%,#e2403f 70%,#7aa0e6)" role="img" aria-label="Woman lying in a glowing tanning bed"></div>
  <div class="prod-title" style="left:614px;top:325px">Tanning Beds</div>
  <p class="prod-text" style="left:614px;top:380px">Lorem ipsum dolor sit amet, consectetur adipiscing elit, sed do eiusmod tempor incididunt ut labore et dolore magna aliquaLorem ipsum dolor sit amet, consectetur adipiscing elit, sed do eiusmod tempor i</p>
  <a class="btn" style="left:614px;top:482px;width:140px;height:38px">Learn More →</a>

  <div class="prod-title" style="left:208px;top:850px">Hydro Massage</div>
  <p class="prod-text" style="left:208px;top:905px">Lorem ipsum dolor sit amet, consectetur adipiscing elit, sed do eiusmod tempor incididunt ut labore et dolore magna aliquaLorem ipsum dolor sit amet, consectetur adipiscing elit, sed do eiusmod tempor i</p>
  <a class="btn" style="left:208px;top:1005px;width:140px;height:38px">Learn More →</a>
  <div class="photo" style="left:643px;top:697px;width:352px;height:433px;background:linear-gradient(180deg,#8b8f7a,#b9c2c8 50%,#dfe8ef)" role="img" aria-label="Woman relaxing in a bubbling water massage tub"></div>

  <div class="photo" style="left:163px;top:1215px;width:352px;height:433px;background:linear-gradient(150deg,#fbe6e2,#f1a29a 45%,#e5524a 75%,#f7d7d3)" role="img" aria-label="Woman resting under a red light therapy bed"></div>
  <div class="prod-title" style="left:603px;top:1363px">Red Light Beds</div>
  <p class="prod-text" style="left:603px;top:1418px">Lorem ipsum dolor sit amet, consectetur adipiscing elit, sed do eiusmod tempor incididunt ut labore et dolore magna aliquaLorem ipsum dolor sit amet, consectetur adipiscing elit, sed do eiusmod tempor</p>
  <a class="btn" style="left:603px;top:1523px;width:140px;height:38px">Learn More →</a>
</section>

<section class="specialist" role="img" aria-label="Dimly lit tanning salon room">
  <svg class="abs" style="left:560px;top:0" width="80" height="24"><path d="M0 0h80L40 24z" fill="#f3f3f6"/></svg>
  <h2>Speak To a Specialist</h2>
  <p>Questions about products, pricing, or availability? Speak to a Veltaro sales specialist now and get the answers you're looking for.</p>
  <a class="btn" style="left:780px;top:139px;width:252px;height:46px">Speak To A Specialist Now</a>
</section>

<section class="industries">
  <h2 class="section-title" style="top:2922px">Endless Industry Applications</h2>
  <div class="card" style="left:160px;top:3023px"><div class="icon"></div><h3>HOUSING</h3><p>Set your community apart from the rest by offering an array of amenities to your residents. Whether it's commercial tanning equipment or the HydroLune, the world's first and only trackless water massage bed</p><div class="more"><span class="circle">→</span>Learn More</div></div>
  <div class="card" style="left:462px;top:3023px"><div class="icon"></div><h3>MEDICAL</h3><p>Veltaro offers a diverse range of well--ness equipment specifically designed for medical facilities, enabling them to offer patients alternative treatment options. Our extensive product lineup includes the HydroLune water massage therapy</p><div class="more"><span class="circle">→</span>Learn More</div></div>
  <div class="card" style="left:765px;top:3023px"><div class="icon"></div><h3>FITNESS</h3><p>Veltaro's cutting-edge equipment empowers fitness enthusiasts to elevate their training routine to new heights. Enhance your facility by incorporating the HydroLunethe industry's first and only trackless water massage</p><div class="more"><span class="circle">→</span>Learn More</div></div>
  <div class="card" style="left:160px;top:3445px"><div class="icon"></div><h3>BEAUTY/SPA</h3><p>Distinguish yourself as a premier industry leader in your region by providing an array of our exquisite luxury wellness equipment. Enhance your spa packages by incorporating our state-of-the-art LumaDerm red light</p><div class="more"><span class="circle">→</span>Learn More</div></div>
  <div class="card" style="left:462px;top:3445px"><div class="icon"></div><h3>TANNING</h3><p>Whether you're embarking on a new salon venture or seeking to upgrade your existing equipment, Veltaro offers a diverse selection of exceptional commercial tanning beds and booths that cater to every guest's</p><div class="more"><span class="circle">→</span>Learn More</div></div>
  <div class="card" style="left:765px;top:3445px"><div class="icon"></div><h3>HOSPITALITY</h3><p>The days of relying solely on room rentals for revenue are behind us. Elevate your guests' experience by providing a range of on-site upgrades, including the groundbreaking HydroLune trackless water massage therapy bed</p><div class="more"><span class="circle">→</span>Learn More</div></div>
  <a class="btn" style="left:452px;top:3873px;width:138px;height:39px">View All</a>
  <a class="btn" style="left:609px;top:3873px;width:139px;height:39px">Contact Us</a>
</section>

<section class="salon">
  <h2>“Starting A Salon Or Spa?”</h2>
  <div class="sub">“We've done it 100s of Times and Will Help You”</div>
  <div class="step" style="top:4285px"><i></i>Develop a Business Plan</div>
  <div class="step" style="top:4345px"><i></i>Space Design</div>
  <div class="step" style="top:4412px"><i></i>Review Financing Options</div>
  <div class="step" style="top:4470px"><i></i>Starup Marketing</div>
  <a class="btn" style="left:160px;top:4543px;width:140px;height:40px">Learn More →</a>
  <div class="photo" style="left:655px;top:4120px;width:385px;height:507px;border-radius:14px;background:linear-gradient(180deg,#d9cbb9,#efe7dc 45%,#c9c2bb 80%,#a9a6a4)" role="img" aria-label="Bright salon interior with pink styling chairs"></div>
</section>

<footer class="footer">
  <div class="brand" style="left:113px;top:112px;font-size:50px;color:var(--white)">Veltaro</div>
  <div class="contact" style="top:200px"><span>⌖</span><span><b>Veltaro Canada</b><br>1180 Birchview Rd, Unit 4,<br>Hamilton, ON L8K 2R3</span></div>
  <div class="contact" style="top:265px"><span>✆</span><span><b>Sales :</b> 555-214-0400</span></div>
  <div class="contact" style="top:297px"><span>✆</span><span><b>Parts &amp; Services :</b> 800-555-0148</span></div>
  <div class="contact" style="top:330px"><span>✆</span><span><b>Main Line :</b> 800-555-0192</span></div>

  <h4 style="left:450px;top:105px">Quick Links</h4>
  <div class="links" style="left:450px;top:135px">• Home<br>• Tanning<br>• Massage<br>• Red Light<br>• Salon Startup<br>• About Us<br>• Contact Us</div>
  <div class="links" style="left:598px;top:135px">• Privacy Policy<br>• Customer Service<br>• Blog<br>• Terms of Service</div>

  <h4 style="left:826px;top:105px">Stay Connected</h4>
  <div class="social" style="left:826px"></div><div class="social" style="left:870px"></div><div class="social" style="left:914px"></div><div class="social" style="left:958px"></div><div class="social" style="left:1002px"></div><div class="social" style="left:1046px"></div>
  <div class="search">Let us help you find what you need</div>

  <p class="legal">Tanning 510(k) K000000 • Contraindication: This Product Is Contraindicated For Use On Persons Under The Age Of 18 Years. *Contraindication: This Product Must Not Be Used If Skin Lesions Or Open Wounds Are Present.* *Warning: This Product Should Not Be Used On Individuals Who Have Had Skin Cancer Or Have A Family History Of Skin Cancer.* *Warning: Persons Repeatedly Exposed To UV Radiation Should Be Regularly Evaluated For Skin Cancer.*<br><br>*Veltaro reserves the right to change design and specifications without notice.</p>
  <div class="copy">© 2023 Veltaro Canada. All Rights Reserved.</div>
</footer>

</body>
</html>
```